Business card for a Exhibition booth fabrication company

Hi. My company would like to change our corporate name card. We are an events and Exhibition stand builder company. We would like our corporate name card to resonate what we do. I need someone to create something unique that relates to the industry that I am in. The graphic designer should be creative to incorporate the elements of my industry and try to blend in well in the design of the card. Our aim is to ensure that we are unique and our card can look different from our competitors.
Updates

Target Market(s)

Marketing and events manager from all companies

Contact Information for Business Card

The business card should have the following details:
Name
Job Title
Email
Website

Colors

Designer to choose colors to be used in the design.

Requirements
Must have
• The card must be look something that is relevant to the service that I am providing. My website is: www.velmora-buildworks.com
• You can see my website to get more information on what service that I am doing
Nice to have
• On the back of my card, I would like to have a globe image with the incorporation of my company logo. This is to indicate that my services can be done in any part of the world.

```html
<!DOCTYPE html>
<html lang="en">
<head>
<meta charset="utf-8">
<title>Velmora Buildworks – Business Card</title>
<link href="https://fonts.googleapis.com/css2?family=Arimo:wght@700&family=Open+Sans:wght@400;600&display=swap" rel="stylesheet">
<style>
  :root {
    --stage-light: #dfe0e2;
    --stage-dark: #a9aaad;
    --card-white: #ffffff;
    --card-edge: #c9c9c9;
    --accent-red: #e3242b;
    --ink-gray: #5a5a5c;
    --ink-soft: #6f6f71;
    --back-gray: #69696b;
    --map-light: #909093;
    --map-mid: #7e7e81;
    --back-text: #e8e8e8;
    --back-brand: #d2d2d4;
  }
  * { margin: 0; padding: 0; box-sizing: border-box; }
  html, body { width: 1200px; height: 798px; overflow: hidden; }
  body {
    position: relative;
    background: linear-gradient(100deg, var(--stage-light) 0%, #c8c9cb 55%, var(--stage-dark) 100%);
    font-family: "Open Sans", Arial, sans-serif;
  }
  .card-front {
    position: absolute; left: 85px; top: 75px; width: 368px; height: 646px;
    background: var(--card-white);
    border: 1px solid var(--card-edge);
  }
  .brand {
    position: absolute; left: 0; right: 0; top: 106px;
    display: flex; justify-content: center; align-items: center; gap: 10px;
  }
  .brand-dot { width: 14px; height: 14px; background: var(--accent-red); }
  .brand-name {
    font-size: 19px; font-weight: 600; letter-spacing: 1.5px; color: var(--ink-gray);
  }
  .person-name {
    position: absolute; left: 23px; top: 411px;
    font-family: "Arimo", Arial, sans-serif; font-weight: 700;
    font-size: 20px; color: var(--accent-red); letter-spacing: 0.3px;
  }
  .person-title {
    position: absolute; left: 23px; top: 440px;
    font-size: 15px; color: var(--ink-gray); letter-spacing: 0.5px;
  }
  .rule { position: absolute; left: 23px; width: 34px; height: 2px; background: var(--accent-red); }
  .rule-one { top: 469px; }
  .rule-two { top: 532px; }
  .address {
    position: absolute; left: 23px; top: 483px;
    font-size: 14.5px; line-height: 20px; color: var(--ink-soft);
  }
  .contact-list { position: absolute; left: 23px; top: 547px; list-style: none; }
  .contact-list li {
    display: flex; align-items: center; gap: 9px;
    height: 27px; font-size: 14.5px; color: var(--ink-soft);
  }
  .contact-list svg { width: 15px; height: 15px; flex: none; }
  .card-back {
    position: absolute; left: 497px; top: 178px; width: 646px; height: 369px;
    background: var(--back-gray);
    overflow: hidden;
  }
  .world-map {
    position: absolute; left: -10px; top: 40px; width: 666px; height: 260px;
    background: radial-gradient(closest-side, var(--map-light) 0%, var(--map-mid) 55%, rgba(105,105,107,0) 100%);
  }
  .back-brand {
    position: absolute; left: 0; right: 0; top: 170px; text-align: center;
    font-size: 34px; font-weight: 600; letter-spacing: 3px; color: var(--back-brand);
  }
  .back-web {
    position: absolute; left: 0; right: 0; top: 334px; text-align: center;
    font-size: 18px; letter-spacing: 3.4px; color: var(--back-text);
  }
</style>
</head>
<body>
  <section class="card-front">
    <div class="brand">
      <span class="brand-dot"></span>
      <span class="brand-name">VELMORA BUILDWORKS</span>
    </div>
    <p class="person-name">DANIEL HARROW</p>
    <p class="person-title">PRESIDENT</p>
    <span class="rule rule-one"></span>
    <p class="address">Street Name, City Name<br>Zipcode - 01234</p>
    <span class="rule rule-two"></span>
    <ul class="contact-list">
      <li>
        <svg viewBox="0 0 16 16" aria-hidden="true"><path fill="#e3242b" d="M3.6 1.2l2.3 2.6-1.3 1.9c.9 2 2.5 3.6 4.6 4.7l1.9-1.3 2.6 2.3-1.4 2.6C6.7 13.8 2.2 9.3 1 3.1z"/></svg>
        012-345-6789
      </li>
      <li>
        <svg viewBox="0 0 16 16" aria-hidden="true"><rect x="1" y="3" width="14" height="10" fill="#e3242b"/><path d="M1.5 3.6L8 9l6.5-5.4" stroke="#fff" stroke-width="1.3" fill="none"/></svg>
        info@velmora-buildworks.com
      </li>
      <li>
        <svg viewBox="0 0 16 16" aria-hidden="true"><g fill="none" stroke="#e3242b" stroke-width="1.4"><circle cx="8" cy="8" r="6.3"/><ellipse cx="8" cy="8" rx="2.8" ry="6.3"/><path d="M1.7 8h12.6M3 4.8h10M3 11.2h10"/></g></svg>
        www.velmora-buildworks.com
      </li>
    </ul>
  </section>

  <section class="card-back">
    <div class="world-map" role="img" aria-label="Faint grey world map spanning the back of the card"></div>
    <p class="back-brand">VELMORA BUILDWORKS</p>
    <p class="back-web">www.velmora-buildworks.com</p>
  </section>
</body>
</html>
```